Keystonery Billboard - Financial Services Company (Investments, Tax Planning and Insurance)

Our new office has a billboard directly above the office building. We'd like something eye-catching with a strong Call to Action, with the main part of the billboard being under 7 words if possible. We'd like you to include a way to get ahold of us (either our website keystoneryllc.example or our phone number 302-418-2907. You may also include in small font something to indicate that we've been serving the area since 1980 (the DE area, the tri-state area, the Marlowe Hollow, etc.)

We offer financial planning, tax planning, and insurance, and we help our clients to focus on their goals and happiness by providing everything they need for lifelong wealth under one roof.

Our logos are attached, we use a triangle logo with green and gray. We use the tagline "discover lasting prosperity" but this does not need to be included.

Potential ideas we have seen from other financial companies-
- the concept that the driver spends more time looking at billboards than planning for their retirement
-something along the lines of "everything you need for your finances is in this building right here" planning, investments, taxes, insurance"
-don't spend your time worrying about retirement, let us help you plan for it
-are you working for your money, or is it working for you?
- retirement takes planning, we're here to help
- ready to retire? talk to us
- need investment advice?
- need help investing?
- crossing your fingers isn't a retirement plan. we can help.
- retiring soon? you need help.

Those are just general ideas, please feel free to be creative.

brand colors:
#00b585
#00b185
#000000
#ffffff
#6d6f75
#6d6f75
#6f7074
#021712
#052e24

```html
<!DOCTYPE html>
<html lang="en">
<head>
<meta charset="utf-8">
<title>Keystonery Billboard</title>
<link rel="stylesheet" href="https://fonts.googleapis.com/css2?family=Montserrat:wght@700;800&family=Tinos:wght@700&display=swap">
<style>
  :root {
    --green-deep: #02412c;
    --green-mid: #1f7f55;
    --green-light: #66f1a3;
    --green-accent: #0b9a60;
    --green-bar: #03432d;
    --mint: #6ff0a5;
    --white: #ffffff;
    --gray: #6d6f75;
    --page: #d9d9d9;
    --gold-a: #f6d445;
    --gold-b: #c99a14;
  }
  * { margin: 0; padding: 0; box-sizing: border-box; }
  html, body { width: 1000px; height: 1200px; overflow: hidden; }
  body { background: var(--page); position: relative; font-family: "Montserrat", sans-serif; }

  .billboard {
    position: absolute; left: 30px; top: 365px;
    width: 940px; height: 469px;
    background: var(--white);
    box-shadow: 0 14px 30px rgba(0,0,0,0.35);
    overflow: hidden;
  }
  .hero {
    position: absolute; left: 0; top: 10px; width: 940px; height: 316px;
    background: linear-gradient(90deg, var(--green-deep) 0%, var(--green-deep) 22%, var(--green-mid) 52%, var(--green-light) 88%, var(--green-light) 100%);
  }
  .url-tab {
    position: absolute; right: 0; top: 0; width: 430px; height: 72px;
  }
  .url {
    position: absolute; right: 38px; top: 16px;
    font-size: 26px; font-weight: 800; color: var(--green-accent);
    line-height: 34px; white-space: nowrap;
  }
  .url .tld { font-weight: 700; color: var(--gray); }
  .headline {
    position: absolute; left: 45px; top: 38px;
    font-size: 71px; font-weight: 800; line-height: 89px;
    color: var(--white); letter-spacing: -0.5px; white-space: nowrap;
  }
  .dollar-art {
    position: absolute; left: 775px; top: 108px; width: 130px; height: 200px;
    border-radius: 40px;
    background: radial-gradient(ellipse at 40% 35%, var(--gold-a) 0%, var(--gold-b) 75%, rgba(201,154,20,0) 100%);
  }
  .services {
    position: absolute; left: 0; top: 326px; width: 940px; height: 76px;
    background: linear-gradient(90deg, #ececec, #ffffff 50%, #ececec);
    display: flex; align-items: center; justify-content: space-between;
    padding: 0 45px;
    font-family: "Tinos", serif; font-weight: 700; font-size: 42px; color: var(--gray);
  }
  .services .divider { width: 3px; height: 30px; background: var(--green-accent); }
  .contact-bar {
    position: absolute; left: 0; top: 402px; width: 940px; height: 67px;
    background: var(--green-bar);
    display: flex; align-items: center; padding: 0 45px; color: var(--white);
  }
  .phone-icon { width: 40px; height: 40px; margin-right: 8px; flex: none; }
  .phone { font-size: 38px; font-weight: 800; letter-spacing: -0.5px; white-space: nowrap; }
  .contact-bar .divider { width: 2px; height: 32px; background: var(--white); margin: 0 18px 0 22px; flex: none; }
  .cta { font-size: 24px; font-weight: 800; white-space: nowrap; }
  .cta .highlight { color: var(--mint); }
</style>
</head>
<body>
  <div class="billboard">
    <div class="hero">
      <svg class="url-tab" viewBox="0 0 430 72" aria-hidden="true">
        <polygon points="0,0 430,0 430,72 38,72" fill="#ffffff"/>
      </svg>
      <div class="url">keystoneryllc<span class="tld">.example</span></div>
      <h1 class="headline">WORRYING<br>ABOUT YOUR<br>MONEY? US TOO!</h1>
      <div class="dollar-art" role="img" aria-label="Gold 3D dollar sign illustration"></div>
    </div>
    <div class="services">
      <span>Planning</span><span class="divider"></span>
      <span>Investments</span><span class="divider"></span>
      <span>Taxes</span><span class="divider"></span>
      <span>Insurance</span>
    </div>
    <div class="contact-bar">
      <svg class="phone-icon" viewBox="0 0 40 40" aria-hidden="true">
        <circle cx="20" cy="20" r="19" fill="#ffffff"/>
        <path d="M13 11 l5 -1 2 6 -3 2 c1.5 3 3.5 5 6 6 l2 -3 6 2 -1 5 c-9 1 -18 -8 -17 -17z" fill="#03432d"/>
      </svg>
      <span class="phone">302-418-2907</span>
      <span class="divider"></span>
      <span class="cta">No worry for a <span class="highlight">free consultation</span></span>
    </div>
  </div>
</body>
</html>
```